NZ First of it's kind solutions directory and marketplace for busy Mums needs a business card design

We need a business card design for our new nationwide business in NZ (long term plans to go global). We provide solutions to the everyday challenges that busy Mums face by connecting them with quality communities and suppliers of carefully selected, relevant products and services. We sell direct via our online marketplace. The final design should communicate our values of inclusivity, quality and smart solutions. Colours should incorporate our logo colour palette of #477077 and #6ba8b2. Our website is at https://www.brightnestmums.example

Target Market(s)

busy Mums, Age 28 – 50, female, income over $100K, location main centres NZ primarily but NZ wide. Is likely juggling work or career with a young family. Probably had hobbies which have fallen by the wayside.
-Wants to succeed in her chosen career without compromising on family life
-to successfully juggle her career without feeling like she is compromising her children
- Is time poor, something always has to give and it’s generally her health (she’ll stay up late, get stressed)
- probably ex corporate or professional career. Has discretional income

Industry/Entity Type

Business

Contact Information for Business Card

Lena Forbisher, Founder, BrightNestMums.example (Strapline Tap; Gather; Sorted), 47 Kowhai Terrace, Ellerslie, Auckland 1051, New Zealand. Mob: 021 483 517 Ph: +64 (0)9 571 4860

Font styles to use
Other font styles liked:
• Raleway, and/or Architects Daughter

Colors
00a990
33b8a4
86cfc6
cfeae6

Requirements
Must have
• the above details, streamline. the logo and colours associated with those logos
Should not have
• foil or metallic colours

```html
<!DOCTYPE html>
<html lang="en">
<head>
<meta charset="utf-8">
<title>BrightNestMums – Business Card</title>
<link href="https://fonts.googleapis.com/css2?family=Roboto+Condensed:wght@400;700&family=Roboto:wght@400&display=swap" rel="stylesheet">
<style>
  :root {
    --bg: #2a2a2a;
    --card-front: #f1f1f1;
    --teal-dark: #477077;
    --teal-light: #6ba8b2;
    --text-grey: #505050;
    --white: #ffffff;
    --shadow-soft: #e3e4e3;
  }
  * { margin: 0; padding: 0; box-sizing: border-box; }
  html, body {
    width: 1200px; height: 960px; overflow: hidden;
    background: var(--bg);
  }
  .stage { position: relative; width: 1200px; height: 960px; }

  .card {
    position: absolute;
    width: 600px; height: 343px;
    border-radius: 22px;
    overflow: hidden;
  }
  .card--front { left: 314px; top: 113px; background: var(--card-front); }
  .card--back  { left: 311px; top: 472px; background: var(--teal-light); }

  /* front */
  .brand-disc {
    position: absolute; left: 40px; top: 90px;
    width: 175px; height: 175px; border-radius: 50%;
    background: var(--teal-dark);
  }
  .brand-disc-shadow {
    position: absolute; left: 54px; top: 302px;
    width: 146px; height: 28px; border-radius: 50%;
    background: var(--shadow-soft);
  }
  .edge-tab {
    position: absolute; right: 0; top: 57px;
    width: 14px; height: 38px; background: var(--teal-dark);
  }
  .contact {
    position: absolute; right: 52px; top: 54px;
    text-align: right;
    font-family: "Roboto", sans-serif;
    color: var(--text-grey);
  }
  .contact__name {
    font-family: "Roboto Condensed", sans-serif;
    font-weight: 700; font-size: 22px; line-height: 26px;
    color: var(--teal-dark); letter-spacing: 0.2px;
  }
  .contact__role {
    font-family: "Roboto Condensed", sans-serif;
    font-weight: 400; font-size: 16px; line-height: 18px;
    color: var(--teal-light); letter-spacing: 0.5px;
  }
  .contact__address {
    margin-top: 28px; font-size: 14.5px; line-height: 19px;
  }
  .contact__lines { margin-top: 8px; list-style: none; }
  .contact__lines li {
    font-size: 14.5px; line-height: 19px;
    display: flex; justify-content: flex-end; align-items: center; gap: 6px;
  }
  .contact__lines li .nb { margin-right: -18px; }
  .contact__icon { width: 13px; height: 13px; margin-right: -19px; flex: none; }
  .contact__lines li span { margin-right: 0; }

  .wordmark {
    display: flex; align-items: center; gap: 10px;
    font-family: "Roboto Condensed", sans-serif; font-weight: 700;
    color: var(--teal-dark);
  }
  .wordmark__dot { border-radius: 50%; background: currentColor; flex: none; }
  .wordmark--front { position: absolute; right: 52px; top: 252px; font-size: 32px; }
  .wordmark--front .wordmark__dot { width: 26px; height: 26px; }

  /* back */
  .wordmark--back {
    position: absolute; left: 0; right: 0; top: 145px;
    justify-content: center; font-size: 44px; color: var(--white);
  }
  .wordmark--back .wordmark__dot { width: 38px; height: 38px; background: var(--teal-dark); }
  .strapline {
    position: absolute; left: 0; right: 0; top: 285px;
    text-align: center;
    font-family: "Roboto", sans-serif; font-size: 14.5px;
    color: var(--white);
  }
</style>
</head>
<body>
<main class="stage">
  <section class="card card--front" aria-label="Card front">
    <div class="brand-disc-shadow"></div>
    <div class="brand-disc" role="img" aria-label="Brand emblem area"></div>
    <div class="edge-tab"></div>

    <div class="contact">
      <p class="contact__name">LENA FORBISHER</p>
      <p class="contact__role">FOUNDER</p>
      <p class="contact__address">47 Kowhai Terrace, Ellerslie<br>Auckland 1051, New Zealand.</p>
      <ul class="contact__lines">
        <li>+64 (0)9 571 4860
          <svg class="contact__icon" viewBox="0 0 16 16" aria-hidden="true"><path fill="#477077" d="M3.6 1.2l2.2 2.6c.3.4.3.9 0 1.3L4.7 6.3c.9 2 2.9 4 5 5l1.2-1.1c.4-.3.9-.3 1.3 0l2.6 2.2c.4.3.4.9.1 1.3l-1.2 1.2C10.7 16 .1 5.4 1.1 2.4L2.3 1.1c.4-.3 1-.3 1.3.1z"/></svg>
        </li>
        <li>021 483 517
          <svg class="contact__icon" viewBox="0 0 16 16" aria-hidden="true"><rect x="4" y="0.8" width="8" height="14.4" rx="1.4" fill="none" stroke="#477077" stroke-width="1.6"/><rect x="5.6" y="3" width="4.8" height="8.4" fill="#477077"/></svg>
        </li>
        <li>BrightNestMums.example
          <svg class="contact__icon" viewBox="0 0 16 16" aria-hidden="true"><circle cx="8" cy="8" r="7" fill="#477077"/><path d="M1.5 8h13M8 1c-2.6 3-2.6 11 0 14M8 1c2.6 3 2.6 11 0 14" stroke="#f1f1f1" stroke-width="1" fill="none"/></svg>
        </li>
      </ul>
    </div>

    <div class="wordmark wordmark--front"><span class="wordmark__dot"></span>BrightNestMums</div>
  </section>

  <section class="card card--back" aria-label="Card back">
    <div class="wordmark wordmark--back"><span class="wordmark__dot"></span>BrightNestMums</div>
    <p class="strapline">Tap; Gather; Sorted</p>
  </section>
</main>
</body>
</html>
```